Visitenkarten-Design für Sonnen-/Fensterschutz
Zielgruppe
KLW GmbH ist eine Firma, die Sonnenschutz und Fensterschutz anbieten.
'Ihr kompetenter Partner in Sachen Sonnenschutz- , Fenster- und Türtechnik. Sie erhalten echtes Handwerk aus dem Mühlviertel zu fairen Preisen.'
Unsere Zielgruppe sind Personen mit Haus, die am Land leben.
Firmenname: KLW GmbH
Slogan: Fenster & Sonnenschutz
Aufgabenstellung
Hier befindet sich das Logodesign: https://dx.qv/t-QwLpo7RbNs
Bitte ein schlichtes Design bereitstellen mit einer Dummy-Person:
Jonas Weidlinger + Telefonnummer + Email
Die finalen Daten bitte erst am Schluss berücksichtigen (für Gewinnerdesign)
Gerne auch hintern + vorne bedruckbar bereitstellen.

```html
<!DOCTYPE html>
<html lang="de">
<head>
<meta charset="utf-8">
<title>KLW GmbH – Visitenkarte</title>
<link rel="stylesheet" href="https://fonts.googleapis.com/css2?family=Open+Sans:wght@400&family=Poppins:wght@400;500;600&family=Orbitron:wght@700&display=swap">
<style>
  :root{
    --stage:#575757;
    --card:#ffffff;
    --ink:#4a4a4a;
    --ink-dark:#111111;
    --orange:#ec6a26;
    --red:#d7262a;
    --glass:#cfdff0;
    --band-text:#fbe3d6;
  }
  html,body{margin:0;padding:0;overflow:hidden;}
  body{width:1200px;height:1200px;background:var(--stage);position:relative;font-family:"Poppins",sans-serif;}
  .card{position:absolute;left:247px;width:668px;height:431px;background:var(--card);overflow:hidden;}
  .card--front{top:112px;}
  .card--back{top:618px;}

  .brand{position:absolute;display:flex;align-items:center;gap:12px;font-family:"Poppins",sans-serif;font-weight:600;color:var(--orange);white-space:nowrap;}
  .brand__mark{display:block;background:var(--orange);}
  .card--front .brand{left:322px;top:62px;font-size:44px;}
  .card--front .brand__mark{width:46px;height:46px;}
  .card--back .brand{left:30px;top:150px;font-size:40px;}
  .card--back .brand__mark{width:42px;height:42px;}

  .divider{position:absolute;left:323px;top:168px;width:3px;height:244px;background:linear-gradient(to bottom,transparent,var(--orange) 15%,var(--orange) 85%,transparent);}

  .person{position:absolute;left:0;width:328px;top:232px;text-align:center;font-family:"Open Sans",sans-serif;color:var(--ink);}
  .person__name{font-size:24px;line-height:30px;margin:0;font-weight:400;}
  .person__role{font-size:18px;line-height:24px;margin:2px 0 0;}

  .contact{position:absolute;left:390px;top:180px;color:var(--ink);font-size:19px;line-height:25px;}
  .contact__company{margin:0 0 2px 18px;font-size:17px;font-weight:500;}
  .contact__row{display:flex;align-items:flex-start;gap:4px;margin-top:11px;}
  .contact__row:first-of-type{margin-top:0;}
  .contact__icon{width:22px;height:22px;flex:none;margin-top:2px;fill:var(--red);}
  .contact__row p{margin:0;}

  .labels{position:absolute;left:336px;top:127px;margin:0;padding:0;list-style:none;font-family:"Poppins",sans-serif;font-weight:500;font-size:15px;line-height:20px;color:var(--ink-dark);}
  .labels li{height:62px;}

  .window-illustration{position:absolute;left:486px;top:58px;width:142px;height:230px;background:linear-gradient(to right,rgba(215,38,42,.55),var(--glass) 45%,rgba(236,106,38,.45));}

  .band{position:absolute;left:0;bottom:0;width:100%;height:86px;background:linear-gradient(to right,var(--orange),var(--red) 85%);display:flex;align-items:center;justify-content:center;}
  .band__slogan{margin:0;font-family:"Orbitron",sans-serif;font-weight:700;font-size:31px;letter-spacing:2px;color:var(--band-text);}
</style>
</head>
<body>

<section class="card card--front">
  <div class="brand"><span class="brand__mark"></span>KLW GmbH</div>
  <div class="divider"></div>

  <div class="person">
    <h1 class="person__name">Jonas Weidlinger</h1>
    <p class="person__role">Geschäftsführer</p>
  </div>

  <div class="contact">
    <p class="contact__company">KLW GmbH</p>
    <div class="contact__row">
      <svg class="contact__icon" viewBox="0 0 24 24" aria-hidden="true"><path d="M2 4 L22 12 L2 20 L7 12 Z"/></svg>
      <p>Am Birkenfeld 21-23<br>30159 Hannover</p>
    </div>
    <div class="contact__row">
      <svg class="contact__icon" viewBox="0 0 24 24" aria-hidden="true"><path d="M6.6 10.8a15 15 0 0 0 6.6 6.6l2.2-2.2a1 1 0 0 1 1-.25 11.4 11.4 0 0 0 3.6.57 1 1 0 0 1 1 1V20a1 1 0 0 1-1 1A17 17 0 0 1 3 4a1 1 0 0 1 1-1h3.5a1 1 0 0 1 1 1c0 1.25.2 2.45.57 3.57a1 1 0 0 1-.25 1z"/></svg>
      <p>+49 152 408 3317</p>
    </div>
    <div class="contact__row">
      <svg class="contact__icon" viewBox="0 0 24 24" aria-hidden="true"><path d="M2 6h20v13H2z M3 7l9 7 9-7" stroke="#fff" stroke-width="1.5"/></svg>
      <p>klwfenster@postfach.de</p>
    </div>
  </div>
</section>

<section class="card card--back">
  <div class="brand"><span class="brand__mark"></span>KLW GmbH</div>

  <ul class="labels">
    <li>SICHTBARES LICHT</li>
    <li>SOLARENERGIE</li>
    <li>STRAHLEN U.V.</li>
  </ul>

  <div class="window-illustration" role="img" aria-label="Illustration: Fensterscheibe, durch die Licht, Solarenergie und UV-Strahlen als Pfeile treten"></div>

  <div class="band"><p class="band__slogan">FENSTER &amp; SONNENSCHUTZ</p></div>
</section>

</body>
</html>
```